Sleek Design For Personal Brand Wordpress Website !!

*WORDPRESS WEBSITE*

Need a sleek and easy to navigate Wordpress website.

It will act as the hub for my personal brand.

Which means it will showcase all my social media outlets, host my most recent content like youtube videos and podcasts...

It will also be the go to place to find all my digital products and services that I offer.

i want it to be super sleek and simple but also give a personal touch of my who I really am. You can get a good idea of who I am my checking out my Instagram (@karim.dulvane)

Use these websites for ideas: www.bronvikel.com and www.teodorplaskewicz.com

Target Market(s)

Young Entrepreneurs

Industry/Entity Type

Education

Logo Text

Karim Dulvane

Number of Pages Required

4 page

Font styles to use
Sans Serif

Colors
ffffff
0392cd
ec1f27

Requirements
Must have
• Social Media buttons on the home page...
• Video (also a slider) right at the top of the home page...
• Email Optin...
• Multiple pages...

```html
<!DOCTYPE html>
<html lang="en">
<head>
<meta charset="utf-8">
<title>Karim Dulvane</title>
<link rel="stylesheet" href="https://fonts.googleapis.com/css2?family=Montserrat:wght@400;600;700;800&family=Open+Sans:wght@400;600;700&display=swap">
<style>
:root{
  --white:#ffffff;
  --blue:#0392cd;
  --red:#ec1f27;
  --ink:#1e1e1e;
  --text:#555a60;
  --muted:#8a8f95;
  --light:#f4f4f4;
  --line:#dcdcdc;
  --dark:#2b2d31;
  --darker:#1f2124;
  --btn-dark:#4a4c50;
}
*{box-sizing:border-box;margin:0;padding:0}
html,body{width:1200px;height:2732px;overflow:hidden}
body{font-family:"Open Sans",Arial,sans-serif;color:var(--text);background:var(--white)}
h1,h2,h3,h4,.brand,.nav{font-family:"Montserrat",Arial,sans-serif}

/* header */
.site-header{height:40px;display:flex;align-items:center;justify-content:space-between;padding:0 160px;background:var(--white);position:relative}
.brand{display:flex;align-items:center;gap:8px;color:var(--red);font-size:18px;font-weight:700;line-height:1;white-space:nowrap}
.brand-mark{width:12px;height:12px;background:var(--red);display:inline-block}
.nav{display:flex;gap:34px;font-size:10px;font-weight:600;letter-spacing:.5px;color:var(--muted)}
.nav a{color:inherit;text-decoration:none;position:relative;padding:13px 0}
.nav a.active{color:var(--red)}
.nav a.active::after{content:"";position:absolute;left:-6px;right:-6px;bottom:0;height:3px;background:var(--red)}

/* hero */
.hero{height:504px;background:linear-gradient(110deg,#8f9298 0%,#c9c6c0 30%,#b9a99a 48%,#d8d6d2 62%,#9ea3a7 100%);border-bottom:4px solid var(--red)}

/* section title */
.section-title{text-align:center;font-size:28px;font-weight:800;color:var(--ink);text-transform:uppercase;letter-spacing:.5px}
.divider{display:block;margin:14px auto 0}

/* about */
.about{height:516px;background:var(--light);padding-top:72px}
.about-body{display:flex;gap:80px;padding:0 160px;margin-top:70px}
.profile-card{width:340px;flex-shrink:0;height:240px;background:var(--white);border:1px solid var(--line);display:flex;padding:20px;gap:22px}
.profile-photo{width:130px;flex-shrink:0;height:198px;background:linear-gradient(160deg,#d7dde3,#8d949c)}
.profile-card h3{font-size:26px;font-weight:600;color:var(--blue);margin-top:10px}
.profile-card p{font-size:11px;line-height:17px;margin-top:14px}
.welcome{flex:1;padding-top:20px}
.welcome h2{font-size:30px;font-weight:400;color:var(--ink)}
.welcome .lead{font-size:12px;font-weight:700;color:var(--blue);line-height:17px;margin-top:16px;text-transform:uppercase}
.welcome p{font-size:12px;line-height:19px;margin-top:16px}

/* training */
.training{height:408px;background:var(--white);padding-top:68px}
.training .section-title{font-size:30px}
.cards{display:flex;gap:40px;padding:0 160px;margin-top:44px}
.card{flex:1}
.card-box{height:120px;border:1px solid var(--line);padding:18px 16px}
.card-box h4{font-size:11px;font-weight:700;color:var(--ink);line-height:15px;text-transform:uppercase}
.card-box p{font-size:11px;line-height:16px;margin-top:10px}
.btn{display:inline-block;margin-top:40px;padding:9px 20px;font-family:"Montserrat",Arial,sans-serif;font-size:11px;font-weight:700;color:var(--white);background:var(--btn-dark);text-transform:uppercase}
.btn.primary{background:var(--blue)}

/* social */
.social{height:532px;position:relative;padding-top:64px}
.social-bg{position:absolute;inset:0;background:linear-gradient(180deg,#2a2c30 0%,#4a4a4c 45%,#3a3030 70%,#1c1d20 100%)}
.social .section-title{position:relative;color:var(--white);text-transform:none;font-size:30px;font-weight:700}
.social-grid{position:relative;display:grid;grid-template-columns:repeat(3,270px);gap:32px 20px;justify-content:center;margin-top:44px}
.tile{height:160px;background:var(--red);display:flex;flex-direction:column;align-items:center;justify-content:center;color:var(--white)}
.tile .mark{width:56px;height:56px;border:4px solid var(--white);border-radius:50%}
.tile span{font-size:13px;margin-top:22px}

/* contact */
.contact{height:448px;background:var(--white);padding-top:104px}
.contact .section-title{text-transform:none;font-size:30px;font-weight:700}
.optin{width:704px;margin:56px auto 0;border:1px solid var(--line);box-shadow:0 2px 8px rgba(0,0,0,.08)}
.optin-head{background:var(--red);color:var(--white);text-align:center;font-family:"Montserrat",Arial,sans-serif;font-size:11px;font-weight:700;padding:12px 0;text-transform:uppercase}
.optin-form{display:flex;gap:14px;padding:30px 28px;background:var(--white)}
.field{flex:1;height:40px;border:1px solid var(--line);font-size:11px;color:var(--muted);padding:12px}
.send{width:70px;height:40px;border:2px solid var(--blue);color:var(--blue);font-family:"Montserrat",Arial,sans-serif;font-size:12px;font-weight:700;display:flex;align-items:center;justify-content:center}

/* footer */
.site-footer{height:252px;background:var(--dark);padding:32px 160px 0;display:flex;gap:80px;color:#b9bcc0}
.footer-col{flex:1}
.footer-col h4{font-size:18px;font-weight:600;color:var(--white);text-transform:uppercase;display:flex;align-items:center;gap:8px}
.footer-col ul{list-style:none;margin-top:22px}
.footer-col li{font-size:12px;line-height:22px}
.addr{display:flex;gap:10px;font-size:12px;line-height:18px;margin-top:18px}
.follow{display:flex;align-items:center;gap:10px;margin-top:26px;font-size:12px}
.sq{width:26px;height:26px;display:inline-block}
.copyright{height:32px;background:var(--darker);text-align:center;font-size:11px;color:var(--muted);line-height:32px}
.copyright b{color:var(--red);font-weight:600}
</style>
</head>
<body>

<header class="site-header">
  <div class="brand"><i class="brand-mark"></i>Karim Dulvane</div>
  <nav class="nav">
    <a class="active">HOME</a><a>EVENT</a><a>PODCAST</a><a>MEDIA PRESS</a><a>BLOG</a><a>CONTACT</a>
  </nav>
</header>

<section class="hero" role="img" aria-label="Photo of Karim Dulvane standing in a bright modern interior"></section>

<section class="about">
  <h2 class="section-title">About Karim Dulvane</h2>
  <svg class="divider" width="120" height="12" viewBox="0 0 120 12" aria-hidden="true"><rect x="0" y="5" width="120" height="2" fill="#0392cd"/><rect x="54" y="0" width="12" height="12" fill="#0392cd"/></svg>
  <div class="about-body">
    <div class="profile-card">
      <div class="profile-photo" role="img" aria-label="Portrait of Karim Dulvane in sunglasses"></div>
      <div>
        <h3>Hi I am</h3>
        <p>Young founder sharing lessons on online stores, products and growth. Every week I post new videos and notes for builders.</p>
      </div>
    </div>
    <div class="welcome">
      <h2>Welcome To Karim Dulvane</h2>
      <p class="lead">Learn how to start an online store, find winning products and grow real traffic with simple steps that work.</p>
      <p>This site gathers my videos, podcasts and guides in one place so you can follow the journey and pick up the tools that helped me build my brand from zero.</p>
      <p>Browse the training below, join the list for updates and reach out any time with questions about your own project and next moves.</p>
    </div>
  </div>
</section>

<section class="training">
  <h2 class="section-title">What you will learn on this free training:</h2>
  <svg class="divider" width="120" height="12" viewBox="0 0 120 12" aria-hidden="true"><rect x="0" y="5" width="120" height="2" fill="#0392cd"/><rect x="54" y="0" width="12" height="12" fill="#0392cd"/></svg>
  <div class="cards">
    <div class="card">
      <div class="card-box"><h4>How you create a store that converts</h4><p>Setting up a clean store, picking a theme and writing pages that turn visitors into buyers.</p></div>
      <a class="btn primary">Learn More</a>
    </div>
    <div class="card">
      <div class="card-box"><h4>How you find hot &amp; trending products to cash out on</h4><p>Simple ways to spot rising items early and test them before spending money on stock.</p></div>
      <a class="btn">Learn More</a>
    </div>
    <div class="card">
      <div class="card-box"><h4>How you can drive large targeted traffic</h4><p>Paid and free channels that bring the right people to your store at a low daily cost.</p></div>
      <a class="btn">Learn More</a>
    </div>
  </div>
</section>

<section class="social">
  <div class="social-bg" role="img" aria-label="Dark photo of a private jet on the tarmac"></div>
  <h2 class="section-title">Stay In Touch With Me.</h2>
  <svg class="divider" width="120" height="12" viewBox="0 0 120 12" aria-hidden="true" style="position:relative"><rect x="0" y="5" width="120" height="2" fill="#0392cd"/><rect x="54" y="0" width="12" height="12" fill="#0392cd"/></svg>
  <div class="social-grid">
    <div class="tile"><i class="mark"></i><span>My favorite place. Quotes.</span></div>
    <div class="tile"><i class="mark"></i><span>Documenting my life through</span></div>
    <div class="tile"><i class="mark"></i><span>My biggest platform. Join</span></div>
    <div class="tile"><i class="mark"></i><span>The most direct &amp; personal way</span></div>
    <div class="tile"><i class="mark"></i><span>My business profile. Keywords</span></div>
    <div class="tile"><i class="mark"></i><span>Perfect for your commute.</span></div>
  </div>
</section>

<section class="contact">
  <h2 class="section-title">Want to get in touch with me?</h2>
  <svg class="divider" width="120" height="12" viewBox="0 0 120 12" aria-hidden="true"><rect x="0" y="5" width="120" height="2" fill="#0392cd"/><rect x="54" y="0" width="12" height="12" fill="#0392cd"/></svg>
  <div class="optin">
    <div class="optin-head">Show me exactly how you did it</div>
    <div class="optin-form">
      <div class="field">First Name</div>
      <div class="field">Last Name</div>
      <div class="field">Email</div>
      <div class="send">SEND</div>
    </div>
  </div>
</section>

<footer class="site-footer">
  <div class="footer-col">
    <h4>Company</h4>
    <ul><li>Privacy Policy</li><li>Terms Condition</li><li>Support</li><li>Contact us</li></ul>
  </div>
  <div class="footer-col">
    <h4><svg width="14" height="20" viewBox="0 0 14 20" aria-hidden="true"><path d="M7 0C3.1 0 0 3.1 0 7c0 5 7 13 7 13s7-8 7-13c0-3.9-3.1-7-7-7z" fill="#0392cd"/><circle cx="7" cy="7" r="2.6" fill="#2b2d31"/></svg>Contact Us</h4>
    <div class="addr"><span>Office 12, Harbor Lane<br>Westbridge Quarter</span></div>
    <div class="addr"><span>Studio 4, Kelm Street<br>North Avenue District</span></div>
  </div>
  <div class="footer-col">
    <h4>Support</h4>
    <div class="follow">Social Network
      <i class="sq" style="background:#2fa6de"></i><i class="sq" style="background:#3b5a9a"></i><i class="sq" style="background:#0f7bb5"></i><i class="sq" style="background:#d9452f"></i>
    </div>
    <ul><li>Mail: hello@dulvane.com</li></ul>
  </div>
</footer>
<div class="copyright">Copyright 2017 <b>Karim Dulvane</b>. All Rights Reserved.</div>

</body>
</html>
```